Very new and innovative Web design for Property managers of Vacation rentals

We are looking for a new website design for travel agencies and property managers specialised on vacation rentals business, holiday villas and apartments.

The end users of this website are travellers who are looking for a vacation home for their next holiday: this is the reason why the website must be easy to use, attractive, professional, possibly elegant and focused on get new reservations.

This is a draft of our current website: https://intro3.kelumsito.com/
Please consider that we would like to have proposals with a totally different and innovative layout, surprise us!

These are the pages of the website:
• Homepage: feel free to redesign all the homepage as you wish, surprise us with something very new! Please consider that Property manager/Travel agencies usually want to have the opportunity to put in evidence groups of houses with specific characteristics (eg. villas with private swimming pool, apartment in big/small towns, villas with air co, etc…), destinations and tourist areas, and sometimes experiences or activities (please consider that the website layout must be suitable even if some of the previous sections are not used).
• Search page: we’d like to organise the results of the search page in three different ways:
o Grid
o Map
o List
• Property page: to illustrate the characteristics, descriptions, images, …. of the property. It is very important to put in evidence images of the property and to maintain the booking form (and the other call to action bottom – eg. whatsapp) always visible
• Custom pages: static pages composed usually by text, images and call to actions
• Contact us (general form)
• Info request (specific of a property form)
• Booking process
• Blog, organised in four pages:
o Home Page – introduction to the blog
o List of articles
o Single article
o Site Map (presentation of categories and sub-categories)

If possible, we’d prefer to receive the material in Adobe XD or similar so that we can obtain the three versions:
- smartphone
- tablet
- desktop

The website will be then developed in Bootstrap: as a result we’ll need the icons in SVG format (or the library used)

In attachment you can find the map of the website pages

```html
<!DOCTYPE html>
<html lang="en">
<head>
<meta charset="utf-8">
<title>StayNest – Exclusive Villas in Italy</title>
<link href="https://fonts.googleapis.com/css2?family=Lato:ital,wght@0,400;0,700;0,900;1,700&display=swap" rel="stylesheet">
<style>
:root{
  --green:#1fa866;
  --dark:#111111;
  --ink:#222222;
  --muted:#555555;
  --gray:#efefef;
  --white:#ffffff;
  --star:#f2891d;
}
*{box-sizing:border-box;margin:0;padding:0}
html,body{width:1200px;height:3907px;overflow:hidden}
body{font-family:'Lato',sans-serif;color:var(--ink);background:var(--white);position:relative}
.abs{position:absolute}

/* hero */
.hero{left:0;top:0;width:1200px;height:739px;background:linear-gradient(180deg,#3d5a78 0%,#6f7f86 35%,#3f6a7e 62%,#1f6f93 80%,#5d7a86 100%)}
.hero-shade{inset:0;background:rgba(10,20,30,.35)}
.toplinks{right:72px;top:24px;color:#fff;font-size:14px;display:flex;gap:10px}
.nav{left:74px;top:62px;width:1052px;height:106px;background:#fff;display:flex;align-items:center;padding:0 24px}
.brand{display:flex;align-items:center;gap:12px;font-size:38px;font-weight:400;color:var(--ink)}
.brand-dot{width:34px;height:34px;border-radius:50%;background:var(--green)}
.menu{margin-left:auto;display:flex;gap:47px;font-size:16px;font-weight:700;color:var(--ink)}
.menu .active{color:var(--green)}
.hero-title{left:0;width:1200px;top:318px;text-align:center;color:#fff;font-size:48px;font-weight:900}
.field{width:330px;height:52px;background:#fff;display:flex;align-items:center;justify-content:space-between;padding:0 16px;font-size:17px;color:#333}
.search-btn{left:435px;top:528px;width:330px;height:52px;background:var(--green);color:#fff;font-weight:900;font-size:21px;display:flex;align-items:center;justify-content:center}

/* headings */
.sec-title{left:0;width:1200px;text-align:center;color:var(--green);font-size:39px;font-weight:900}
.rule{left:510px;width:179px;height:4px;background:var(--dark)}
.intro{left:60px;width:1080px;top:898px;text-align:center;font-size:16px;line-height:32.5px;color:#222}

.band{left:0;width:1200px;background:var(--gray)}
.card{width:331px;background:#fff}
.card-img{width:331px;height:227px}
.card-body{padding:18px 20px}
.card-name{font-size:16px;font-weight:700;margin-top:4px}
.stars{display:flex;gap:6px;margin-top:12px}
.meta{display:flex;align-items:center;gap:8px;font-size:13px;font-weight:700;margin-top:20px}
.meta b{color:var(--green)}
.price-row{display:flex;justify-content:space-between;align-items:center;margin-top:26px}
.from{font-size:14px;font-style:italic;font-weight:700}
.price{font-size:18px;font-weight:700;color:var(--green)}
.more{width:146px;height:46px;border:2px solid #333;color:var(--green);font-weight:900;font-size:15px;display:flex;align-items:center;justify-content:center}
.arrow{width:30px;height:44px}
.btn-dark{width:203px;height:47px;background:var(--dark);color:#fff;font-size:14px;font-weight:900;display:flex;align-items:center;justify-content:center}

.tile{width:513px;height:349px;overflow:hidden}
.tile-text{position:absolute;left:20px;right:40px;bottom:22px;color:#fff}
.tile-text h3{color:var(--green);font-size:24px;font-weight:900;text-transform:uppercase;margin-bottom:4px}
.tile-text p{font-size:14px;line-height:21px}
.tile-fade{position:absolute;left:0;right:0;bottom:0;height:160px;background:linear-gradient(180deg,rgba(0,0,0,0),rgba(0,0,0,.7))}

.post{width:331px;height:456px;background:#fff}
.post-img{width:331px;height:252px;position:relative}
.date{position:absolute;left:20px;bottom:0;background:#2b2b2b;color:#fff;font-size:14px;font-weight:700;padding:10px 14px;border-radius:6px 6px 0 0}
.post h4{color:var(--green);font-size:19px;font-weight:700;line-height:27px;padding:22px 20px 0}
.post p{font-size:13.5px;line-height:23px;padding:10px 20px 0;color:#333}

.footer{left:0;top:3607px;width:1200px;height:300px;background:var(--dark)}
.news{left:74px;top:3515px;width:1052px;height:126px;background:var(--green);display:flex;align-items:center;padding:0 28px;color:#fff}
.news h5{font-size:22px;font-weight:900;margin-right:12px}
.email{width:400px;height:56px;background:#fff;display:flex;align-items:center;justify-content:space-between;padding:0 18px;color:#333;font-size:16px}
.follow{margin-left:auto;width:245px}
.follow h5{margin-bottom:10px}
.socials{display:flex;gap:26px}
.socials span{width:26px;height:26px;border-radius:50%;background:#fff;display:block}
.fcol{color:#ddd;font-size:14px;line-height:30px}
.fcol h6{color:#fff;font-size:19px;font-weight:900;margin-bottom:10px}
</style>
</head>
<body>

<section class="hero abs" role="img" aria-label="White luxury villa with a swimming pool at dusk"></section>
<div class="hero-shade abs"></div>
<div class="toplinks abs"><span>Login</span><span>/</span><span>Wish List (0)</span><span>/</span><span>Language ▾</span></div>
<header class="nav abs">
  <div class="brand"><span class="brand-dot"></span>StayNest</div>
  <nav class="menu"><span class="active">Home</span><span>Last Minute</span><span>Special Offers</span><span>Experience</span><span>Contact Us</span></nav>
</header>
<h1 class="hero-title abs">EXCLUSIVE VILLAS IN ITALY</h1>
<div class="field abs" style="left:264px;top:397px">Destination</div>
<div class="field abs" style="left:608px;top:397px">Checkin <svg width="14" height="14" viewBox="0 0 14 14"><rect x="1" y="2" width="12" height="11" fill="#222"/><rect x="3" y="5" width="8" height="6" fill="#fff"/></svg></div>
<div class="field abs" style="left:264px;top:464px">Checkout <svg width="14" height="14" viewBox="0 0 14 14"><rect x="1" y="2" width="12" height="11" fill="#222"/><rect x="3" y="5" width="8" height="6" fill="#fff"/></svg></div>
<div class="field abs" style="left:608px;top:464px">Travelers <svg width="16" height="16" viewBox="0 0 16 16"><circle cx="8" cy="5" r="4" fill="#222"/><path d="M1 16c0-5 14-5 14 0z" fill="#222"/></svg></div>
<div class="search-btn abs">SEARCH</div>

<h2 class="sec-title abs" style="top:803px">LOOKING FOR AN EXCLUSIVE HOLIDAY?</h2>
<div class="rule abs" style="top:871px"></div>
<p class="intro abs">Browse our vacation rental selections. If you are looking for a real experiences, our portal is the right solution.<br>Our vacation homes are all located in Italy and we take care of them and their owners at every time. Our goal is give to our guest authentic taste of holiday and our country. Our team is always ready to assure the best time and take care of you!<br>Add a local experience to your stay with us: by diving into our local "network" you can have the unique chance to discover and travel our culture through the eye of a local...!</p>

<section class="band abs" style="top:1124px;height:724px"></section>
<h2 class="sec-title abs" style="top:1198px">NEW VILLAS AND VACATION RENTALS</h2>
<div class="rule abs" style="top:1266px"></div>
<svg class="arrow abs" style="left:32px;top:1513px" viewBox="0 0 30 44"><path d="M24 4L8 22l16 18" stroke="#333" stroke-width="6" fill="none"/></svg>
<svg class="arrow abs" style="left:1138px;top:1513px" viewBox="0 0 30 44"><path d="M6 4l16 18L6 40" stroke="#333" stroke-width="6" fill="none"/></svg>

<div class="card abs" style="left:74px;top:1308px">
  <div class="card-img" role="img" aria-label="Modern villa with pool at sunset" style="background:linear-gradient(180deg,#2e5275,#8a7f6a 55%,#3f9fc4)"></div>
  <div class="card-body">
    <div class="card-name">Farmhouse In Tuscany</div>
    <div class="stars"><svg width="118" height="18" viewBox="0 0 118 18"><g fill="#f2891d"><path id="s" d="M9 0l2.6 6 6.4.5-4.9 4.2 1.5 6.3L9 13.6 3.4 17l1.5-6.3L0 6.5 6.4 6z"/><use href="#s" x="25"/><use href="#s" x="50"/><use href="#s" x="75"/><use href="#s" x="100"/></g></svg></div>
    <div class="meta"><svg width="18" height="12" viewBox="0 0 18 12"><rect x="0" y="0" width="2" height="12" fill="#222"/><rect x="0" y="7" width="18" height="3" fill="#222"/><rect x="5" y="3" width="13" height="4" fill="#222"/></svg>Sleeps : <b>12</b> | Bedroom : <b>4</b></div>
    <div class="price-row"><div><div class="from">From</div><div class="price">€1300/Week</div></div><div class="more">MORE INFO</div></div>
  </div>
</div>
<div class="card abs" style="left:435px;top:1308px">
  <div class="card-img" role="img" aria-label="Stone villa with blue pool and loungers" style="background:linear-gradient(180deg,#4d8fd0,#cfc3a6 55%,#3e98c7)"></div>
  <div class="card-body">
    <div class="card-name">Farmhouse In Tuscany</div>
    <div class="stars"><svg width="118" height="18" viewBox="0 0 118 18"><g fill="#f2891d"><use href="#s"/><use href="#s" x="25"/><use href="#s" x="50"/><use href="#s" x="75"/><use href="#s" x="100"/></g></svg></div>
    <div class="meta"><svg width="18" height="12" viewBox="0 0 18 12"><rect x="0" y="0" width="2" height="12" fill="#222"/><rect x="0" y="7" width="18" height="3" fill="#222"/><rect x="5" y="3" width="13" height="4" fill="#222"/></svg>Sleeps : <b>12</b> | Bedroom : <b>4</b></div>
    <div class="price-row"><div><div class="from">From</div><div class="price">€1300/Week</div></div><div class="more">MORE INFO</div></div>
  </div>
</div>
<div class="card abs" style="left:795px;top:1308px">
  <div class="card-img" role="img" aria-label="Garden pool surrounded by trees" style="background:linear-gradient(180deg,#3f5a2c,#6f8a45 55%,#3c8fc0)"></div>
  <div class="card-body">
    <div class="card-name">Farmhouse In Tuscany</div>
    <div class="stars"><svg width="118" height="18" viewBox="0 0 118 18"><g fill="#f2891d"><use href="#s"/><use href="#s" x="25"/><use href="#s" x="50"/><use href="#s" x="75"/><use href="#s" x="100"/></g></svg></div>
    <div class="meta"><svg width="18" height="12" viewBox="0 0 18 12"><rect x="0" y="0" width="2" height="12" fill="#222"/><rect x="0" y="7" width="18" height="3" fill="#222"/><rect x="5" y="3" width="13" height="4" fill="#222"/></svg>Sleeps : <b>12</b> | Bedroom : <b>4</b></div>
    <div class="price-row"><div><div class="from">From</div><div class="price">€1300/Week</div></div><div class="more">MORE INFO</div></div>
  </div>
</div>
<div class="btn-dark abs" style="left:499px;top:1825px">VIEW ALL VILLAS</div>

<div class="tile abs" style="left:74px;top:1933px" role="img" aria-label="Modern villa with pool under an evening sky">
  <div class="abs" style="inset:0;background:linear-gradient(180deg,#8ea3b8,#b9b9b2 45%,#35617a 75%,#1c2b33)"></div>
  <div class="tile-fade"></div>
  <div class="tile-text"><h3>Luxury Villas</h3><p>This selection of properties includes all the best rentals available. Most with private swimming pool with chef and maid services available.</p></div>
</div>
<div class="tile abs" style="left:616px;top:1933px" role="img" aria-label="Guests relaxing by a resort pool among palm trees">
  <div class="abs" style="inset:0;background:linear-gradient(180deg,#f2d7b8,#d88f5b 45%,#6b4a3a 75%,#2a2522)"></div>
  <div class="tile-fade"></div>
  <div class="tile-text"><h3>Experiences</h3><p>Don't live just a holiday but an experience! Let's discover our services.</p></div>
</div>
<div class="tile abs" style="left:74px;top:2310px" role="img" aria-label="Couple browsing rentals on a laptop">
  <div class="abs" style="inset:0;background:linear-gradient(180deg,#8a6a55,#9d8c80 45%,#5a5450 75%,#1f1d1c)"></div>
  <div class="tile-fade"></div>
  <div class="tile-text"><h3>Browse All Vacation Rentals</h3><p>From here you can browse all the villa selections, you can refine them by using the filters on the search results web page.</p></div>
</div>
<div class="tile abs" style="left:616px;top:2310px" role="img" aria-label="Terrace with curtains overlooking the sea">
  <div class="abs" style="inset:0;background:linear-gradient(180deg,#8a5a3a 0%,#8a5a3a 14%,#4e7fb2 16%,#2f5f90 55%,#4d5a66 75%,#222)"></div>
  <div class="tile-fade"></div>
  <div class="tile-text"><h3>Last Minute Deals</h3><p>Browse all the last minute deals to browse the villas offering discounts for last minute arrivals.</p></div>
</div>

<section class="band abs" style="top:2726px;height:698px"></section>
<h2 class="sec-title abs" style="top:2784px">BLOG POSTS</h2>
<div class="rule abs" style="top:2853px"></div>
<svg class="arrow abs" style="left:32px;top:3124px" viewBox="0 0 30 44"><path d="M24 4L8 22l16 18" stroke="#333" stroke-width="6" fill="none"/></svg>
<svg class="arrow abs" style="left:1138px;top:3124px" viewBox="0 0 30 44"><path d="M6 4l16 18L6 40" stroke="#333" stroke-width="6" fill="none"/></svg>

<article class="post abs" style="left:74px;top:2894px">
  <div class="post-img" role="img" aria-label="Colourful seaside village with boats" style="background:linear-gradient(180deg,#7fb2dc,#d98a6a 45%,#3a7fa8 70%,#1f4f6e)"><span class="date">Apr 02, 2021</span></div>
  <h4>Excepteur sint occaecat non cupidatat proident</h4>
  <p>Sed ut perspiciatis unde omnis iste natus error sit voluptatem accusan tiumdolor emque laudantium, totam rem periam quaerat voluptatem.</p>
</article>
<article class="post abs" style="left:434px;top:2894px">
  <div class="post-img" role="img" aria-label="Villa garden with a pool and slide" style="background:linear-gradient(180deg,#2f5f9e,#4f7a3a 45%,#3fb0d8 75%,#9a8a70)"><span class="date">Apr 02, 2021</span></div>
  <h4>Excepteur sint occaecat non cupidatat proident</h4>
  <p>Sed ut perspiciatis unde omnis iste natus error sit voluptatem accusan tiumdolor emque laudantium, totam rem periam quaerat voluptatem.</p>
</article>
<article class="post abs" style="left:796px;top:2894px">
  <div class="post-img" role="img" aria-label="White modern villa facade with pool" style="background:linear-gradient(180deg,#6f9cc8,#d9d7d0 40%,#8c8276 70%,#4aa5cf)"><span class="date">Apr 02, 2021</span></div>
  <h4>Excepteur sint occaecat non cupidatat proident</h4>
  <p>Sed ut perspiciatis unde omnis iste natus error sit voluptatem accusan tiumdolor emque laudantium, totam rem periam quaerat voluptatem.</p>
</article>
<div class="btn-dark abs" style="left:499px;top:3400px">VIEW ALL POSTS</div>

<footer class="footer abs"></footer>
<div class="news abs">
  <h5>NEWSLETTER SIGN UP</h5>
  <div class="email">Enter Email Address <svg width="20" height="20" viewBox="0 0 20 20"><circle cx="10" cy="10" r="9" fill="var(--green)"/><path d="M8 5l5 5-5 5" stroke="#fff" stroke-width="2.5" fill="none"/></svg></div>
  <div class="follow"><h5>FOLLOW US</h5><div class="socials"><span></span><span></span><span></span><span></span><span></span></div></div>
</div>

<div class="abs" style="left:76px;top:3712px;color:#fff">
  <div class="brand" style="color:#fff;font-size:30px"><span class="brand-dot" style="width:28px;height:28px"></span>StayNest</div>
  <div class="fcol" style="font-size:13px;line-height:25px;margin-top:14px">Copyright © 2021 StayNest.<br>All Rights Reserved.<br>Powered by StayNest</div>
</div>
<div class="fcol abs" style="left:379px;top:3694px"><h6>QUICK LINKS</h6>Last Minute<br>Special Offers<br>Experience<br>Contact Us</div>
<div class="fcol abs" style="left:635px;top:3694px"><h6>COMPANY</h6>Privacy Policies<br>Reservation Policies<br>Cookie Policy</div>
<div class="fcol abs" style="left:883px;top:3694px"><h6>STAYNEST</h6>via dei Cipressi 42<br>50100 Borgo Alto, Siena (Italy)<br>Phone: +39 000 1234567<br>VAT Code: IT00000000000</div>

</body>
</html>
```